Non Profit Company Looking For New Website

The website for Fernvale Quillstone Heritage Society should offer the viewer beautiful photos that inspire condifence and joy and tap into our love of horses.

We would like to see a website that displays trust, quality and confidence. Needs to be responsive and mobile friendly for all browsers and coded for both Android & IOS.

READ ATTACHED WEBSITE TEMPLATE FOR COMPLETE DETAILS ON WHAT WE ARE LOOKING FOR.

Looking for recommmendations if we should use WordPress/WooCommerce for site or Wordpress with Shopify Plug in or just Shopify.

Must be both desktop and mobile friendly with fast page load speed. Need the ability to edit ourselves.

Industry/Entity Type

Non Profit

Coding

Coded - Design and coding required

Number of Pages Required

5+ page

Requirements
Must have
• We would like to see a website that displays trust, quality and confidence. Needs to be responsive and mobile friendly for all browsers and coded for both Android & IOS.

Looking for recommendations if we should use WordPress/WooCommerce for site or Wordpress with Shopify Plug in or just Shopify.

Logo Colour:
Pantone 7621 C

READ TEMPLATE THAT IS ATTACHED
Nice to have
• Like look of this website as a sample:
https://www.quellbrimtorva.com/

Another similar non profit organization
https://pellaworthcindle.com/

```html
<!DOCTYPE html>
<html lang="en">
<head>
<meta charset="utf-8">
<title>Fernvale Quillstone Heritage Society</title>
<link rel="stylesheet" href="https://fonts.googleapis.com/css2?family=Montserrat:wght@500;600&family=Quicksand:wght@400;500;600&display=swap">
<style>
:root{
  --brand:#b01e2e;
  --brand-dark:#8e1424;
  --ink:#1d1d1d;
  --body:#444;
  --muted:#666;
  --line:#d8d8d8;
  --white:#fff;
}
*{margin:0;padding:0;box-sizing:border-box}
html,body{width:1200px;height:3157px;overflow:hidden;background:var(--white)}
body{position:relative;font-family:"Quicksand",sans-serif;color:var(--body)}
.abs{position:absolute}
h1,h2,h3{font-family:"Montserrat",sans-serif;font-weight:600;color:var(--ink)}

.header{position:absolute;left:0;top:0;width:1200px;height:93px;background:var(--white)}
.brand{left:88px;top:20px;width:140px;display:flex;align-items:center;gap:8px;color:var(--brand);font-weight:600;font-size:13px;line-height:16px}
.brand-dot{width:12px;height:12px;border-radius:50%;background:var(--brand);flex:none}
.nav a{position:absolute;top:36px;transform:translateX(-50%);font-size:16px;color:var(--ink);text-decoration:none;font-weight:500;white-space:nowrap}
.nav a.active{color:var(--brand)}

.hero{left:0;top:93px;width:1200px;height:663px;
  background:
    radial-gradient(ellipse 260px 380px at 700px 420px,rgba(90,48,24,.95),rgba(90,48,24,0) 100%),
    radial-gradient(ellipse 200px 260px at 640px 300px,rgba(125,70,38,.9),rgba(125,70,38,0) 100%),
    radial-gradient(ellipse 300px 300px at 1100px 180px,rgba(214,120,70,.85),rgba(214,120,70,0) 100%),
    radial-gradient(ellipse 320px 280px at 120px 120px,rgba(200,110,62,.85),rgba(200,110,62,0) 100%),
    radial-gradient(ellipse 420px 200px at 480px 150px,rgba(220,210,200,.55),rgba(220,210,200,0) 100%),
    linear-gradient(180deg,#9a5d3c 0%,#7a4630 55%,#3e2a22 100%)}
.hero-shade{left:0;top:93px;width:1200px;height:663px;background:linear-gradient(90deg,rgba(0,0,0,.22),rgba(0,0,0,0) 65%)}
.hero-title{left:88px;top:234px;width:705px;font-family:"Quicksand",sans-serif;font-size:25px;line-height:30px;color:var(--white);font-weight:500}
.hero-text{left:88px;top:307px;width:520px;font-size:16.5px;line-height:29px;color:var(--white);font-weight:500}
.btn{position:absolute;display:flex;align-items:center;justify-content:center;border-radius:24px;background:var(--brand);color:var(--white);font-size:17.5px;font-weight:500}
.dot{position:absolute;top:512px;width:10px;height:10px;border-radius:50%;background:var(--white)}
.dot.on{background:var(--brand)}

.about-title{left:88px;top:864px;width:500px;font-size:42px;line-height:41px}
.about-copy{left:88px;top:978px;width:478px;font-size:17px;line-height:30.5px;text-align:justify}
.about-copy p+p{margin-top:30px}
.photo{position:absolute}

.section-title{left:0;width:1200px;text-align:center;font-size:42px}
.tabs span{position:absolute;top:1474px;transform:translateX(-50%);font-family:"Montserrat",sans-serif;font-size:12.5px;font-weight:600;color:var(--ink)}

.give{left:0;top:2179px;width:1200px;height:325px;
  background:
    radial-gradient(ellipse 260px 200px at 380px 90px,rgba(210,80,90,.45),rgba(210,80,90,0) 100%),
    radial-gradient(ellipse 300px 220px at 560px 290px,rgba(120,12,26,.6),rgba(120,12,26,0) 100%),
    linear-gradient(90deg,#a51a2b,#b31f30 40%,#9e1828 70%,#8a1423)}
.btn.light{background:var(--white);color:var(--brand)}

.sub-title{font-size:33px;top:2668px}
.ico{position:absolute;left:89px;width:60px;height:60px}
.info{position:absolute;left:165px;font-size:17.5px;line-height:27px;color:var(--muted)}
.field{position:absolute;left:582px;width:531px;height:46px;border:1px solid var(--line);padding:12px 15px;font-size:17px;color:var(--muted)}

.foot a{position:absolute;top:3086px;transform:translateX(-50%);font-size:14.5px;color:var(--muted);text-decoration:none}
.sep{position:absolute;top:3086px;font-size:14.5px;color:var(--muted)}
.copy{left:0;top:3117px;width:1200px;text-align:center;font-size:13.5px;color:var(--muted)}
</style>
</head>
<body>

<header class="header">
  <div class="abs brand"><span class="brand-dot"></span><span>Fernvale Quillstone Heritage Society</span></div>
  <nav class="nav">
    <a class="active" style="left:428px">Home</a>
    <a style="left:525px">About</a>
    <a style="left:623px">Adopt</a>
    <a style="left:724px">Horses</a>
    <a style="left:855px">Donate/Shop</a>
    <a style="left:990px">Contact</a>
    <a style="left:1090px">En &#8964;</a>
  </nav>
</header>

<div class="abs hero" role="img" aria-label="Photo of a bay horse wearing a halter against blurred autumn trees"></div>
<div class="abs hero-shade"></div>
<h1 class="abs hero-title">We support and develop retired thoroughbred racehorses for their next chapter in life Retire. Retrain. Rehome.</h1>
<p class="abs hero-text">Fernvale Quillstone Heritage Society (FQHS) is a registered not-for-profit organization in Fernvale.</p>
<div class="btn" style="left:88px;top:385px;width:165px;height:43px">Read More</div>
<span class="dot on" style="left:87px"></span>
<span class="dot" style="left:105px"></span>
<span class="dot" style="left:124px"></span>
<span class="dot" style="left:142px"></span>

<h2 class="abs about-title">What is Thoroughbred Aftercare?</h2>
<div class="abs about-copy">
  <p>The health, safety and welfare of our equine athletes does not end at the finish line, and retirement and aftercare are critical to the success of the racing industry.</p>
  <p>Aftercare is the safe placement of racehorses after their careers as racehorse are completed. Some horses might retire to the breeding shed or broodmare bands, while others are retrained for second careers.</p>
</div>
<div class="btn" style="left:88px;top:1259px;width:264px;height:43px">Learn More About Us</div>
<div class="photo" style="left:602px;top:863px;width:501px;height:448px;background:
  radial-gradient(ellipse 110px 170px at 110px 230px,rgba(50,32,26,.85),rgba(50,32,26,0) 100%),
  radial-gradient(ellipse 110px 150px at 330px 260px,rgba(150,80,40,.85),rgba(150,80,40,0) 100%),
  radial-gradient(ellipse 90px 170px at 420px 230px,rgba(90,55,40,.8),rgba(90,55,40,0) 100%),
  linear-gradient(180deg,#2f4422 0%,#4d7a2c 35%,#6fa33a 70%,#86b845 100%)" role="img" aria-label="Photo of three horses, including a foal, walking in a green pasture"></div>

<h2 class="abs section-title" style="top:1400px">Adopt a Horse</h2>
<div class="tabs">
  <span style="left:444px">ALL</span>
  <span style="left:553px">THOROUGHBREDS</span>
  <span style="left:707px">STANDARDBREDS</span>
</div>
<svg class="abs" style="left:440px;top:1490px" width="8" height="7"><polygon points="4,0 8,7 0,7" fill="var(--brand)"/></svg>

<div class="photo" style="left:89px;top:1528px;width:334px;height:241px;background:
  radial-gradient(ellipse 110px 150px at 200px 150px,rgba(150,80,38,.95),rgba(150,80,38,0) 100%),
  radial-gradient(ellipse 60px 90px at 60px 140px,rgba(120,70,40,.7),rgba(120,70,40,0) 100%),
  linear-gradient(180deg,#4f78b0 0%,#6e9a52 45%,#7fa648 100%)" role="img" aria-label="Photo of a chestnut horse with a white blaze"></div>
<div class="photo" style="left:434px;top:1528px;width:333px;height:241px;background:
  radial-gradient(ellipse 70px 120px at 170px 130px,rgba(110,70,45,.9),rgba(110,70,45,0) 100%),
  linear-gradient(180deg,#ece4df 0%,#cfc2bb 45%,#9a9a7a 70%,#7f8a5a 100%)" role="img" aria-label="Photo of a brown horse standing in an open field"></div>
<div class="photo" style="left:778px;top:1528px;width:334px;height:241px;background:
  radial-gradient(ellipse 120px 70px at 180px 120px,rgba(30,22,20,.85),rgba(30,22,20,0) 100%),
  linear-gradient(180deg,#3b74b4 0%,#8fb1d6 50%,#c9d7e2 68%,#8e9c6e 100%)" role="img" aria-label="Photo of a black horse rearing under a blue sky"></div>
<div class="photo" style="left:89px;top:1781px;width:334px;height:240px;background:
  radial-gradient(ellipse 100px 90px at 160px 120px,rgba(150,72,34,.9),rgba(150,72,34,0) 100%),
  linear-gradient(180deg,#a9c3de 0%,#d8c9a0 45%,#c9b050 65%,#a6b83e 100%)" role="img" aria-label="Photo of a chestnut horse with a flaxen mane in a meadow"></div>
<div class="photo" style="left:434px;top:1781px;width:333px;height:240px;background:
  radial-gradient(ellipse 100px 80px at 180px 120px,rgba(120,55,30,.85),rgba(120,55,30,0) 100%),
  linear-gradient(180deg,#cadf96 0%,#9cc866 55%,#79ab45 100%)" role="img" aria-label="Photo of a bay horse galloping on grass"></div>
<div class="photo" style="left:778px;top:1781px;width:334px;height:240px;background:
  radial-gradient(ellipse 150px 140px at 210px 140px,rgba(200,100,45,.9),rgba(200,100,45,0) 100%),
  linear-gradient(120deg,#7a4a22,#b9733a 50%,#e4a865)" role="img" aria-label="Photo of a chestnut horse head in warm sunlight"></div>
<div class="btn" style="left:518px;top:2035px;width:165px;height:43px">Adopt Now</div>

<div class="abs give" role="img" aria-label="Red-tinted photo of a horse"></div>
<h2 class="abs section-title" style="top:2275px;color:var(--white);font-size:40px">Make a Difference</h2>
<div class="btn light" style="left:480px;top:2356px;width:238px;height:45px">More Ways To Give</div>

<h2 class="abs section-title" style="top:2594px">Need More Information</h2>
<h3 class="abs sub-title" style="left:88px">Contact Us</h3>
<h3 class="abs sub-title" style="left:581px">Let’s Talk</h3>

<svg class="ico" style="top:2740px" viewBox="0 0 60 60"><circle cx="30" cy="30" r="28.5" fill="none" stroke="var(--brand)" stroke-width="2"/><path d="M30 22a6 6 0 0 0-6 6c0 4.5 6 11 6 11s6-6.5 6-11a6 6 0 0 0-6-6z" fill="var(--brand)"/><circle cx="30" cy="28" r="2.2" fill="#fff"/></svg>
<p class="info" style="top:2742px;width:360px">Lorem ipsum dolor sit amet, consectetur adipiscing elit, sed do eiusmod</p>
<svg class="ico" style="top:2832px" viewBox="0 0 60 60"><circle cx="30" cy="30" r="28.5" fill="none" stroke="var(--brand)" stroke-width="2"/><path d="M24.5 23.5l3-1 2 4.5-2 1.5a10 10 0 0 0 4 4l1.5-2 4.5 2-1 3c-6 .5-12.5-6-12-12z" fill="var(--brand)"/></svg>
<p class="info" style="top:2834px">Phone Number<br>+1 888 888 888</p>
<svg class="ico" style="top:2924px" viewBox="0 0 60 60"><circle cx="30" cy="30" r="28.5" fill="none" stroke="var(--brand)" stroke-width="2"/><rect x="21" y="24" width="18" height="13" rx="1.5" fill="var(--brand)"/><path d="M21 25l9 7 9-7" fill="none" stroke="#fff" stroke-width="1.6"/></svg>
<p class="info" style="top:2926px">Email Us<br>info@mysite.com</p>

<div class="field" style="top:2743px">Name</div>
<div class="field" style="top:2797px">Email</div>
<div class="field" style="top:2851px">Phone Number</div>
<div class="field" style="top:2905px;height:79px">Message</div>
<div class="btn" style="left:582px;top:2993px;width:165px;height:43px">Submit</div>

<nav class="foot">
  <a style="left:304px">Home</a>
  <span class="sep" style="left:352px">|</span>
  <a style="left:406px">About</a>
  <span class="sep" style="left:455px">|</span>
  <a style="left:509px">Adopt</a>
  <span class="sep" style="left:558px">|</span>
  <a style="left:617px">Horses</a>
  <span class="sep" style="left:673px">|</span>
  <a style="left:751px">Donate/Shop</a>
  <span class="sep" style="left:827px">|</span>
  <a style="left:887px">Contact</a>
</nav>
<p class="abs copy">Copyrights © 2021.All Rights Reserved Privacy Policy</p>

</body>
</html>
```